Brivolt Technologies business card design

We need a business card designed with our new logo. it would be great if the card could communicate it is a technology based company.

Target Market(s)

system integrators

Industry/Entity Type

technology, IOT

Contact Information for Business Card

Name, designation, Address, telephone number, email address

Requirements
Must have
• logo and company name
Nice to have
• something to do with technology

```html
<!DOCTYPE html>
<html lang="en">
<head>
<meta charset="utf-8">
<title>Brivolt Technologies business card</title>
<link rel="stylesheet" href="https://fonts.googleapis.com/css2?family=Open+Sans:wght@400;600;700&display=swap">
<style>
  :root {
    --backdrop: #3a3a3a;
    --card: #161616;
    --card-back: #111111;
    --orange: #f7931e;
    --white: #ffffff;
    --soft-white: #e6e6e6;
  }
  * { box-sizing: border-box; margin: 0; padding: 0; }
  html, body { width: 1200px; height: 801px; overflow: hidden; }
  body {
    background: var(--backdrop);
    font-family: "Open Sans", sans-serif;
    display: flex;
    align-items: center;
    justify-content: center;
    gap: 40px;
  }
  .card {
    position: relative;
    width: 520px;
    height: 297px;
    border-bottom: 3px solid var(--orange);
    border-left: 2px solid var(--orange);
    overflow: hidden;
  }
  .card--front { background: var(--card); }
  .card--back { background: var(--card-back); }

  .brand {
    position: absolute;
    top: 52px;
    right: 60px;
    display: flex;
    align-items: center;
    gap: 10px;
  }
  .brand__mark { width: 16px; height: 16px; background: var(--orange); }
  .brand__name {
    color: var(--white);
    font-weight: 700;
    font-size: 22px;
    letter-spacing: 1.5px;
    text-transform: uppercase;
  }

  .rule-main {
    position: absolute;
    top: 118px;
    left: 200px;
    right: 0;
    height: 1px;
    background: var(--orange);
  }

  .address {
    position: absolute;
    right: 40px;
    top: 140px;
    text-align: right;
    color: var(--white);
    font-size: 13px;
    line-height: 1.45;
  }

  .person {
    position: absolute;
    left: 36px;
    top: 150px;
    width: 230px;
  }
  .person__name {
    color: var(--orange);
    font-weight: 700;
    font-size: 19px;
    text-transform: uppercase;
    letter-spacing: 0.3px;
  }
  .person__title { color: var(--white); font-size: 13px; margin-top: 2px; }
  .person__rule { height: 1px; background: var(--orange); margin: 12px 0 10px; }

  .contacts { list-style: none; }
  .contacts li {
    display: flex;
    align-items: center;
    gap: 8px;
    color: var(--white);
    font-size: 12.5px;
    line-height: 1.6;
  }
  .contacts svg { width: 11px; height: 11px; flex: none; }

  .pattern-area {
    position: absolute;
    inset: 0;
    background: linear-gradient(135deg, #0b0b0b 0%, #1a1a1a 55%, #262626 100%);
  }
  .back-brand {
    position: absolute;
    right: 70px;
    top: 120px;
    display: flex;
    align-items: center;
    gap: 10px;
  }
</style>
</head>
<body>
  <section class="card card--front">
    <div class="brand">
      <span class="brand__mark"></span>
      <span class="brand__name">Brivolt Technologies</span>
    </div>
    <div class="rule-main"></div>
    <p class="address">1870 Harbor Crest Way<br>Seal Cove CA 90410</p>
    <div class="person">
      <h1 class="person__name">Daniel Roarke</h1>
      <p class="person__title">President</p>
      <div class="person__rule"></div>
      <ul class="contacts">
        <li>
          <svg viewBox="0 0 12 12" aria-hidden="true"><path fill="#f7931e" d="M2.4 1l2 2.2-1 1.3a7 7 0 0 0 4.1 4.1l1.3-1 2.2 2-1 1.4C5.5 11 1 6.5 1 2z"/></svg>
          555-014-2278
        </li>
        <li>
          <svg viewBox="0 0 12 12" aria-hidden="true"><rect x="0.5" y="2" width="11" height="8" fill="#f7931e"/><path d="M0.5 2.5L6 6.5l5.5-4" fill="none" stroke="#161616" stroke-width="1"/></svg>
          info@brivolttech.com
        </li>
        <li>
          <svg viewBox="0 0 12 12" aria-hidden="true"><circle cx="6" cy="6" r="5" fill="none" stroke="#f7931e" stroke-width="1.4"/><path d="M1 6h10M6 1c-2.5 3-2.5 7 0 10M6 1c2.5 3 2.5 7 0 10" fill="none" stroke="#f7931e" stroke-width="1"/></svg>
          www.brivolttech.com
        </li>
      </ul>
    </div>
  </section>

  <section class="card card--back">
    <div class="pattern-area" role="img" aria-label="Repeating tonal pattern of the brand mark in glossy black"></div>
    <div class="back-brand">
      <span class="brand__mark"></span>
      <span class="brand__name">Brivolt</span>
    </div>
  </section>
</body>
</html>
```